Website Header Development

I am after a redesign of the Header of a website www.tlvoltaris.com.au.
This project is for the header only, and should fit in with the rest of the site
Target Market(s)
Business
Requirements
Should not have
- Over the top. Keep it simple

```html
<!DOCTYPE html>
<html lang="en">
<head>
<meta charset="utf-8">
<title>TL Voltaris – Resource Efficiency</title>
<link href="https://fonts.googleapis.com/css2?family=Alegreya:wght@700&family=Alegreya+Sans:wght@400;700&display=swap" rel="stylesheet">
<style>
:root{
  --page-bg:#f9f9f9;
  --sheet:#ffffff;
  --sky-top:#b9d3ee;
  --sky-mid:#dbe7f5;
  --sky-low:#9fb6dc;
  --nav-dark:#1a7a3a;
  --nav-light:#3a8f42;
  --navy:#0e1e8a;
  --brand-blue:#1d3b8c;
  --side-blue:#213f95;
  --ink:#1b1b1b;
  --field-line:#c9c9c9;
}
*{box-sizing:border-box;margin:0;padding:0}
html,body{width:1200px;height:472px;overflow:hidden;background:var(--page-bg)}
.site{position:absolute;left:142px;top:0;width:916px;height:472px;background:var(--sheet);overflow:hidden;font-family:"Alegreya Sans",sans-serif;color:var(--ink)}
.masthead{position:absolute;left:0;top:0;width:916px;height:105px;border-top:2px solid var(--brand-blue)}
.masthead-art{position:absolute;inset:0;background:linear-gradient(to bottom,var(--sky-top),var(--sky-mid) 55%,var(--sky-low))}
.brand{position:absolute;left:0;width:916px;top:42px;text-align:center;font-family:"Alegreya Sans",sans-serif;font-weight:700;font-size:31px;color:var(--brand-blue);letter-spacing:0.5px}
.brand-mark{position:absolute;left:445px;top:-35px;width:26px;height:26px;border-radius:50%;background:var(--brand-blue)}
.main-nav{position:absolute;left:0;top:105px;width:916px;height:49px;background:linear-gradient(115deg,var(--nav-dark) 0 12%,var(--nav-light) 12% 88%,var(--nav-dark) 88%)}
.main-nav a{position:absolute;color:#fff;text-decoration:none;font-size:12px;white-space:nowrap}
.main-nav a.major{font-weight:700;font-size:14px;top:22px}
.main-nav a.minor{top:19px}
.page-title{position:absolute;left:0;width:646px;top:180px;text-align:center;font-family:"Alegreya",serif;font-weight:700;font-size:24.5px;color:var(--navy);letter-spacing:0.4px;white-space:nowrap}
.intro{position:absolute;left:55px;top:228px;width:178px;font-size:14px;line-height:23px}
.intro p{margin-bottom:23px}
.feature-photo{position:absolute;left:264px;top:238px;width:320px;height:214px;background:linear-gradient(120deg,#eef1f4,#cfd6dd 55%,#e6e9ec)}
.search{position:absolute;left:674px;top:154px;width:169px;height:29px;border:1px solid var(--field-line);font-family:Arial,sans-serif;font-size:13px;color:#999;padding:6px 0 0 26px}
.search svg{position:absolute;left:8px;top:8px}
.side-title{position:absolute;left:675px;top:216px;width:170px;font-family:"Alegreya",serif;font-weight:700;font-size:19px;line-height:28px;letter-spacing:2px;color:var(--side-blue)}
.side-copy{position:absolute;left:675px;width:175px;font-weight:700;font-size:10px;line-height:23px}
.side-field{position:absolute;left:674px;top:392px;width:169px;height:31px;border:1px solid var(--field-line)}
</style>
</head>
<body>
<div class="site">
  <header class="masthead">
    <div class="masthead-art" role="img" aria-label="Decorative sky banner with slanted green and blue stripes on both sides"></div>
    <div class="brand"><span class="brand-mark"></span>tl voltaris</div>
  </header>
  <nav class="main-nav">
    <a class="major" style="left:77px">Home</a>
    <a class="minor" style="left:146px">About Us</a>
    <a class="minor" style="left:219px">Services</a>
    <a class="minor" style="left:285px">Projects and Case Studies</a>
    <a class="major" style="left:434px">Financial Information</a>
    <a class="minor" style="left:596px">News</a>
    <a class="minor" style="left:651px">Contact</a>
  </nav>

  <h1 class="page-title">Resource Efficiency – Sustainable Solutions</h1>
  <div class="intro">
    <p>Is your business performing as well as your competitors?</p>
    <p>Are your fixed costs comparable to industry leaders?</p>
    <p>Is your business becoming less profitable with increased energy, waste and water prices?</p>
    <p>Do you wish to reduce your</p>
  </div>
  <div class="feature-photo" role="img" aria-label="Photo of a businessman holding up a puzzle piece labelled Solution"></div>

  <aside>
    <div class="search">
      <svg width="13" height="14" viewBox="0 0 13 14" aria-hidden="true"><circle cx="7.5" cy="5.5" r="4" fill="none" stroke="#888" stroke-width="2"/><line x1="5" y1="8.5" x2="1.5" y2="13" stroke="#888" stroke-width="2.4"/></svg>
      Search
    </div>
    <h2 class="side-title">TL Voltaris Newsletter</h2>
    <p class="side-copy" style="top:316px">Would you like to receive our regular monthly Newsletter? Please fill in your Name:</p>
    <div class="side-field"></div>
    <p class="side-copy" style="top:436px">Let us know your email address so we can send the Newsletter directly to</p>
  </aside>
</div>
</body>
</html>
```